BUSINESS CARD DESIGN

NAME- DALE VORSKIN
PHONE NUMER - 555- 714-9082
EMAIL- OFFICE@TRV-GROUNDMAKRZ.COM
BACK OF CARD- SPEACIALIZES IN LAND CLEARING, FORESTRY MUCLHING AND EXCAVATION

Contact Information for Business Card

NAME- DALE VORSKIN PHONE NUMER - 555- 714-9082 EMAIL- OFFICE@TRV-GROUNDMAKRZ.COM BACK OF CARD- SPEACIALIZES IN LAND CLEARING , MUCLHING AND EXCAVATION

```html
<!DOCTYPE html>
<html lang="en">
<head>
<meta charset="utf-8">
<title>Terravale Groundmakrz – Business Card</title>
<link href="https://fonts.googleapis.com/css2?family=Montserrat:wght@400;500;700;800&display=swap" rel="stylesheet">
<style>
  :root {
    --stage: #2b2d31;
    --card-white: #ffffff;
    --card-black: #0b0b0c;
    --ink: #141414;
    --ink-soft: #3a3a3a;
    --accent: #f5a20a;
    --rule: #222222;
    --back-text: #d9d9d9;
  }
  * { box-sizing: border-box; margin: 0; padding: 0; }
  html, body {
    width: 1200px; height: 900px; overflow: hidden;
    background: var(--stage);
    font-family: "Montserrat", sans-serif;
  }
  .stage { position: relative; width: 1200px; height: 900px; }
  .card {
    position: absolute; left: 250px; width: 700px; height: 400px;
    border-radius: 4px;
    box-shadow: 0 14px 30px rgba(0,0,0,.45);
    overflow: hidden;
  }

  /* Front */
  .card-front { top: 40px; background: var(--card-white); }
  .brand {
    position: absolute; left: 300px; top: 30px; width: 320px;
    display: flex; flex-direction: column; align-items: center; gap: 10px;
  }
  .brand-dot {
    width: 96px; height: 96px; border-radius: 50%;
    background: var(--ink);
  }
  .brand-text {
    display: flex; flex-direction: column; align-items: center; gap: 5px; width: 100%;
  }
  .brand-name {
    font-weight: 800; color: var(--ink); font-size: 26px;
    line-height: 1; letter-spacing: .5px; white-space: nowrap;
  }
  .brand-sub {
    font-weight: 700; color: var(--ink); font-size: 14px;
    letter-spacing: 8px; line-height: 1;
  }
  .brand-rule { height: 3px; background: var(--rule); width: 100%; }
  .brand-phone {
    font-weight: 700; font-size: 13px; letter-spacing: 7px; color: var(--ink); line-height: 1;
  }
  .person {
    position: absolute; left: 40px; top: 270px; width: 240px;
  }
  .person-name {
    color: var(--accent); font-weight: 700; font-size: 24px; letter-spacing: -.3px;
    white-space: nowrap;
  }
  .person-title {
    color: var(--ink-soft); font-weight: 500; font-size: 15px; margin-top: 6px;
  }
  .divider {
    position: absolute; left: 280px; top: 262px; width: 3px; height: 92px;
    background: var(--accent);
  }
  .contacts {
    position: absolute; left: 300px; top: 264px; list-style: none;
    display: flex; flex-direction: column; gap: 10px;
  }
  .contact {
    display: flex; align-items: center; gap: 10px;
    font-size: 16px; font-weight: 500; color: var(--ink-soft);
    text-transform: uppercase; white-space: nowrap;
  }
  .contact svg { width: 16px; height: 16px; flex: 0 0 auto; }

  /* Back */
  .card-back { top: 470px; background: var(--card-black); }
  .back-texture {
    position: absolute; inset: 0;
    background: radial-gradient(ellipse at 40% 35%, #1c1c1e 0%, #0b0b0c 70%);
  }
  .back-content {
    position: absolute; left: 50%; top: 50%; transform: translate(-50%, -50%);
    display: flex; flex-direction: column; align-items: center; gap: 16px;
    width: 560px;
  }
  .back-mark { display: flex; align-items: center; gap: 10px; }
  .back-dot { width: 34px; height: 34px; border-radius: 50%; background: #ffffff; }
  .back-name { color: #ffffff; font-weight: 800; font-size: 14px; letter-spacing: 1px; }
  .back-services {
    color: var(--back-text); font-weight: 500; font-size: 12px;
    letter-spacing: 2px; text-transform: uppercase; text-align: center; line-height: 1.6;
  }
</style>
</head>
<body>
<main class="stage">
  <section class="card card-front" aria-label="Business card front">
    <div class="brand">
      <span class="brand-dot"></span>
      <div class="brand-text">
        <span class="brand-name">TERRAVALE GROUNDMAKRZ</span>
        <span class="brand-rule"></span>
        <span class="brand-sub">LLC</span>
        <span class="brand-rule"></span>
        <span class="brand-phone">555.714.9082</span>
      </div>
    </div>

    <div class="person">
      <p class="person-name">DALE VORSKIN</p>
      <p class="person-title">Managing Director</p>
    </div>

    <span class="divider"></span>

    <ul class="contacts">
      <li class="contact">
        <svg viewBox="0 0 24 24" aria-hidden="true"><path fill="#f5a20a" d="M6.6 10.8a15.1 15.1 0 0 0 6.6 6.6l2.2-2.2a1 1 0 0 1 1-.25 11.4 11.4 0 0 0 3.6.57 1 1 0 0 1 1 1V20a1 1 0 0 1-1 1A17 17 0 0 1 3 4a1 1 0 0 1 1-1h3.5a1 1 0 0 1 1 1c0 1.25.2 2.45.57 3.57a1 1 0 0 1-.25 1z"/></svg>
        555- 714-9082
      </li>
      <li class="contact">
        <svg viewBox="0 0 24 24" aria-hidden="true"><path fill="#f5a20a" d="M3 5h18a1 1 0 0 1 1 1v12a1 1 0 0 1-1 1H3a1 1 0 0 1-1-1V6a1 1 0 0 1 1-1zm9 7.2L20 7H4z"/></svg>
        OFFICE@TRV-GROUNDMAKRZ.COM
      </li>
      <li class="contact">
        <svg viewBox="0 0 24 24" aria-hidden="true"><circle cx="12" cy="12" r="9" fill="none" stroke="#f5a20a" stroke-width="2.4"/><path d="M3 12h18M12 3c3 3.5 3 14.5 0 18M12 3c-3 3.5-3 14.5 0 18" fill="none" stroke="#f5a20a" stroke-width="1.8"/></svg>
        WWW.TRV-GROUNDMAKRZ.COM
      </li>
    </ul>
  </section>

  <section class="card card-back" aria-label="Business card back">
    <div class="back-texture" role="img" aria-label="Tonal black pattern of repeated company marks"></div>
    <div class="back-content">
      <div class="back-mark">
        <span class="back-dot"></span>
        <span class="back-name">TERRAVALE GROUNDMAKRZ</span>
      </div>
      <p class="back-services">Specializes in land clearing,<br>forestry mulching and excavation</p>
    </div>
  </section>
</main>
</body>
</html>
```